Varnik Holdings — Business Card Design Brief
Overview
Design a double-sided business card for Varnik Holdings that highlights our two service arms: Varnik Communications (telecommunications) and Varnik Energy (business energy solutions). The card should feel smart and stand out when handed to clients.

Objectives
Showcase our areas of specialty clearly.
Reflect the overall Varnik / Varnik Holdings brand while acknowledging both arms.
Explore using both logos (Communications + Energy) or one unified logo, depending on the design.

Deliverables
One double-sided business card design (front + back).

Content & Copy
Front (preferred): Logo: Varnik / Varnik Holdings
Descriptor: Business Communications | Business Energy
Back:My contact details and company details
Core products: Business Mobile • Telephony • Internet • Business Energy Solutions

Brand & Visual Direction
We have a group logo currently tailored more toward telecoms, plus a separate Varnik Energy logo.
Please explore layouts that use both logos or just one, whichever works best.
Color: I wouldn't mind seeing an option using our the Blue/Purple gradient from our website (varnik-example.co.uk), but also open to non-gradient approaches and other colours..

Overall look: Smart, modern, and distinctive.
Format & Print Specs
Double-sided business card format. (Use a standard size

Must-Haves
Front: Varnik wording or Varnik Holdings wording with atleast 1 logo also on front “Business Communications | Business Energy.”

Back: Contact + company details and core products.
A design that stands out while remaining professional.

Nice-to-Have Options
A gradient version using our site’s Blue/Purple gradient.
A non-gradient version.
A dual-logo treatment versus a single-logo treatment.

Thanks
Owen

```html
<!DOCTYPE html>
<html lang="en">
<head>
<meta charset="utf-8">
<title>Varnik Holdings – Business Card</title>
<link href="https://fonts.googleapis.com/css2?family=Montserrat:wght@800&family=Roboto:wght@400;700&display=swap" rel="stylesheet">
<style>
  :root{
    --bg:#e4e4e4;
    --white:#ffffff;
    --navy:#1c1466;
    --ink:#1b1560;
    --green:#7cc21f;
    --green-dark:#5fae2a;
    --blue:#1a8fe0;
    --blue-deep:#1565d8;
  }
  *{margin:0;padding:0;box-sizing:border-box}
  html,body{width:1200px;height:1200px;overflow:hidden;background:var(--bg)}
  .canvas{position:relative;width:1200px;height:1200px}
  .card{position:absolute;left:255px;width:690px;height:394px;background:var(--white);overflow:hidden;
        box-shadow:0 14px 22px rgba(0,0,0,.18)}
  .card--front{top:160px}
  .card--back{top:654px}
  .card__wave{position:absolute;inset:0}
  .brand{position:absolute;font-family:"Montserrat",sans-serif;font-weight:800;color:var(--ink);
         letter-spacing:1px;line-height:1;white-space:nowrap}
  .brand-dot{position:absolute;border-radius:50%}
  .descriptor{position:absolute;font-family:"Roboto",sans-serif;white-space:nowrap;line-height:1}
  .front-brand{left:68px;top:218px;font-size:52px}
  .front-dot{left:98px;top:130px;width:72px;height:72px;border:9px solid var(--green)}
  .front-descriptor{left:78px;top:277px;font-size:15px;letter-spacing:3.3px;color:var(--green-dark)}
  .details{position:absolute;right:40px;top:0;text-align:right;font-family:"Roboto",sans-serif;color:var(--white)}
  .details p{position:absolute;right:0;white-space:nowrap;line-height:1}
  .name{top:52px;font-size:27px;font-weight:700;color:var(--green);letter-spacing:.5px}
  .title{top:81px;font-size:16px}
  .addr1{top:119px;font-size:16.5px}
  .addr2{top:139px;font-size:16.5px}
  .contact{font-size:16px;padding-right:28px}
  .c1{top:173px}.c2{top:193px}.c3{top:213px}.c4{top:234px}
  .contact svg{position:absolute;right:0;top:1px;width:15px;height:15px}
  .service{font-size:17px;padding-right:16px}
  .service::after{content:"";position:absolute;right:2px;top:7px;width:5px;height:5px;border-radius:50%;background:var(--white)}
  .s1{top:263px}.s2{top:284px}.s3{top:306px}.s4{top:327px}
  .back-dot{left:311px;top:88px;width:68px;height:68px;background:var(--blue-deep)}
  .back-brand{left:0;right:0;text-align:center;top:210px;font-size:60px}
  .back-descriptor{left:0;right:0;text-align:center;top:284px;font-size:16px;color:var(--blue-deep)}
</style>
</head>
<body>
<div class="canvas">

  <section class="card card--front">
    <svg class="card__wave" viewBox="0 0 690 394" aria-hidden="true">
      <defs>
        <linearGradient id="arcBlue" x1="0" y1="0" x2="0" y2="1">
          <stop offset="0" stop-color="#1e63d6"/>
          <stop offset=".5" stop-color="#1aa3e8"/>
          <stop offset="1" stop-color="#1e63d6"/>
        </linearGradient>
      </defs>
      <path d="M246 0 Q556 197 266 394 L690 394 L690 0 Z" fill="url(#arcBlue)"/>
      <path d="M256 0 Q566 197 276 394 L690 394 L690 0 Z" fill="#1c1466"/>
    </svg>

    <span class="brand-dot front-dot"></span>
    <p class="brand front-brand">VARNIK</p>
    <p class="descriptor front-descriptor">BUSINESS ENERGY</p>

    <div class="details">
      <p class="name">DANIEL REEVE</p>
      <p class="title">President</p>
      <p class="addr1">2140 Alder Crescent</p>
      <p class="addr2">Halden, Canada 48215</p>
      <p class="contact c1">555-210-4836
        <svg viewBox="0 0 16 16"><path d="M3.5 1.5l2.5 3-1.5 1.8c.9 1.9 2.3 3.3 4.2 4.2L10.5 9l3 2.5-1.2 2.3C7 13.5 2.5 9 2.2 3.7z" fill="#7cc21f"/></svg></p>
      <p class="contact c2">555-318-7290
        <svg viewBox="0 0 16 16"><rect x="4" y="1" width="8" height="14" rx="1.2" fill="none" stroke="#7cc21f" stroke-width="1.8"/></svg></p>
      <p class="contact c3">info@varnik-example.com
        <svg viewBox="0 0 16 16"><rect x="1.5" y="3.5" width="13" height="9" fill="#7cc21f"/><path d="M1.5 3.5L8 9l6.5-5.5" fill="none" stroke="#1c1466" stroke-width="1.2"/></svg></p>
      <p class="contact c4">www.varnik-example.com
        <svg viewBox="0 0 16 16"><circle cx="8" cy="8" r="6.5" fill="#7cc21f"/><path d="M4 5c2 0 2 2 4 2s1 3 0 4M10 3c0 2 2 2 3 3" fill="none" stroke="#1c1466" stroke-width="1.2"/></svg></p>
      <p class="service s1">Business Mobile</p>
      <p class="service s2">Telephony</p>
      <p class="service s3">Internet</p>
      <p class="service s4">Business Energy Solutions</p>
    </div>
  </section>

  <section class="card card--back">
    <span class="brand-dot back-dot"></span>
    <p class="brand back-brand">VARNIK</p>
    <p class="descriptor back-descriptor">BUSINESS COMMUNICATIONS</p>
  </section>

</div>
</body>
</html>
```